Create a memorable Stationary for Security Software Company

Velbrantix is the worldwide leader in securing the Internet. Making Internet communications and critical data secure, reliable and available everywhere has been and continues to be our ongoing vision. We are committed to staying focused on real customer needs and to developing new and innovative security solutions that redefine the security landscape.

Industry/Entity Type

Internet

Font styles to use
Serif
Sans Serif
Script

Colors
0792cd
33a6d7
85cae6

```html
<!DOCTYPE html>
<html lang="en">
<head>
<meta charset="utf-8">
<title>Velbrantix Business Card</title>
<link href="https://fonts.googleapis.com/css2?family=Open+Sans:wght@400;600&display=swap" rel="stylesheet">
<style>
  :root {
    --bg: #e9e9eb;
    --card: #161617;
    --blue-deep: #0792cd;
    --blue: #33a6d7;
    --blue-light: #85cae6;
    --text: #f2f2f2;
    --rule: #6b6b6e;
  }
  * { margin: 0; padding: 0; box-sizing: border-box; }
  html, body {
    width: 1200px; height: 814px; overflow: hidden;
    background: var(--bg);
    font-family: "Open Sans", Arial, sans-serif;
  }
  .stage {
    position: relative; width: 1200px; height: 814px;
    display: flex; align-items: center; justify-content: center; gap: 40px;
  }
  .card {
    position: relative; width: 540px; height: 309px;
    background: var(--card);
    box-shadow: 0 6px 18px rgba(0,0,0,.25);
  }
  .brand {
    display: flex; align-items: center; gap: 12px;
  }
  .brand-dot {
    width: 22px; height: 22px; border-radius: 50%;
    background: var(--blue);
  }
  .brand-name {
    font-weight: 600; font-size: 30px; color: var(--blue);
    letter-spacing: .5px;
  }
  /* front */
  .card-front .brand { position: absolute; left: 40px; top: 136px; }
  .card-front .brand-name { font-size: 27px; }
  .divider {
    position: absolute; left: 262px; top: 40px; width: 1px; height: 230px;
    background: linear-gradient(to bottom, transparent, var(--rule) 20%, var(--rule) 80%, transparent);
  }
  .details {
    position: absolute; left: 290px; top: 58px; color: var(--text);
    font-size: 14px; line-height: 20px;
  }
  .person-name { color: var(--blue); font-size: 18px; font-weight: 600; line-height: 24px; }
  .person-role { margin-bottom: 8px; }
  .address { margin-bottom: 6px; }
  .contact-list { list-style: none; }
  .contact-list li { display: flex; align-items: center; gap: 10px; height: 21px; }
  .contact-list svg { width: 13px; height: 13px; fill: var(--blue-deep); flex: none; }
  /* back */
  .card-back .brand {
    position: absolute; left: 0; right: 0; top: 112px; justify-content: center;
  }
  .web {
    position: absolute; left: 0; right: 0; top: 232px; text-align: center;
    color: var(--blue-deep); font-size: 13px; letter-spacing: 4px;
  }
</style>
</head>
<body>
<main class="stage">
  <section class="card card-front">
    <div class="brand">
      <span class="brand-dot"></span>
      <span class="brand-name">Velbrantix</span>
    </div>
    <div class="divider"></div>
    <div class="details">
      <p class="person-name">Maren Holt</p>
      <p class="person-role">CEO/Founder</p>
      <p class="address">4120 Larchmont Way<br>Fairbrook, Oregon 97031</p>
      <ul class="contact-list">
        <li><svg viewBox="0 0 16 16"><path d="M3.5 1l3 3-1.8 1.8c.9 2 2.5 3.6 4.5 4.5L11 8.5l3 3-2 3C6 14 2 10 1.5 3.5z"/></svg>541 208 7713</li>
        <li><svg viewBox="0 0 16 16"><rect x="4" y="1" width="8" height="4"/><rect x="1" y="6" width="14" height="6" rx="1"/><rect x="4" y="10" width="8" height="5"/></svg>541 208 7714</li>
        <li><svg viewBox="0 0 16 16"><path d="M1 3h14v1.5L8 9 1 4.5z"/><path d="M1 6.2L8 10.7l7-4.5V13H1z"/></svg>hello@velbrantix.net</li>
        <li><svg viewBox="0 0 16 16"><circle cx="8" cy="8" r="7"/></svg>www.velbrantix.net</li>
      </ul>
    </div>
  </section>

  <section class="card card-back">
    <div class="brand">
      <span class="brand-dot"></span>
      <span class="brand-name">Velbrantix</span>
    </div>
    <p class="web">www.velbrantix.net</p>
  </section>
</main>
</body>
</html>
```